Whitcombe Business Card Design

The name of the business is Dario Whitcombe, CPA LLC
The service that we offer is Accounting, Tax & Consulting Services. I need it to have the following items:
Dario Whitcombe, Principal
Phone Number
Email Address
Physical Address

I have attached the company logo, one in black and one in white. Please provide a design in black background and the other in white background. Please include "Accounting, Tax & Consulting Services". I want the business card to be clean and very professional.

```html
<!DOCTYPE html>
<html lang="en">
<head>
<meta charset="utf-8">
<title>Dario Whitcombe, CPA LLC – Business Cards</title>
<link href="https://fonts.googleapis.com/css2?family=Rajdhani:wght@500;600;700&family=Rubik:wght@400;500&display=swap" rel="stylesheet">
<style>
  :root {
    --backdrop: #1b1b1c;
    --card-dark: #363638;
    --card-light: #ffffff;
    --brand-red: #9b1419;
    --ink: #3a3a3c;
    --ink-soft: #6a6a6c;
    --band-dark: #333335;
    --on-dark: #f2f2f2;
  }
  * { box-sizing: border-box; margin: 0; padding: 0; }
  html, body {
    width: 1200px; height: 874px; overflow: hidden;
    background: var(--backdrop);
  }
  .stage {
    position: relative; width: 1200px; height: 874px;
  }
  .card {
    position: absolute; left: 285px; width: 630px; height: 360px;
    overflow: hidden;
  }

  /* Back of card (dark) */
  .card--back { top: 57px; background: var(--card-dark); }
  .back-lockup {
    position: absolute; left: 0; right: 0; top: 120px;
    display: flex; align-items: center; justify-content: center; gap: 14px;
  }
  .back-lockup .mark-square {
    width: 26px; height: 26px; background: var(--on-dark);
  }
  .back-lockup .firm-name {
    font-family: "Rajdhani", sans-serif; font-weight: 700;
    font-size: 38px; letter-spacing: 2px; color: var(--on-dark);
    text-transform: uppercase;
  }
  .tagline {
    position: absolute; left: 0; right: 0; top: 232px; text-align: center;
    font-family: "Rajdhani", sans-serif; font-weight: 700; font-size: 16px;
    letter-spacing: 1.2px; color: var(--on-dark); text-transform: uppercase;
  }

  /* Front of card (light) */
  .card--front { top: 437px; background: var(--card-light); }
  .red-tab {
    position: absolute; right: 118px; top: 0; width: 56px; height: 40px;
    background: var(--brand-red);
  }
  .front-lockup {
    position: absolute; right: 40px; top: 62px;
    display: flex; align-items: center; gap: 10px;
  }
  .front-lockup .mark-square { width: 16px; height: 16px; background: var(--brand-red); }
  .front-lockup .firm-name {
    font-family: "Rajdhani", sans-serif; font-weight: 700; font-size: 23px;
    letter-spacing: 1px; color: var(--ink); text-transform: uppercase;
  }
  .front-lockup + .credential {
    position: absolute; right: 40px; top: 96px;
    font-family: "Rubik", sans-serif; font-size: 13px; letter-spacing: 3px;
    color: var(--ink-soft); text-transform: uppercase;
  }
  .person {
    position: absolute; left: 58px; top: 112px;
  }
  .person-name {
    font-family: "Rajdhani", sans-serif; font-weight: 700; font-size: 36px;
    color: var(--brand-red); text-transform: uppercase; letter-spacing: 1px; line-height: 1;
  }
  .person-title {
    font-family: "Rubik", sans-serif; font-size: 16px; color: var(--ink-soft);
    margin-top: 2px;
  }
  .rule {
    position: absolute; left: 58px; right: 40px; top: 176px; height: 2px;
    background: var(--brand-red);
  }
  .contact-list {
    position: absolute; left: 58px; top: 192px; list-style: none;
    font-family: "Rubik", sans-serif; font-size: 15px; color: var(--ink);
  }
  .contact-list li { display: flex; align-items: center; gap: 10px; height: 25px; }
  .contact-list svg { width: 13px; height: 13px; fill: var(--brand-red); flex: none; }
  .address {
    position: absolute; right: 40px; top: 192px; text-align: right;
    font-family: "Rubik", sans-serif; font-size: 15px; line-height: 25px; color: var(--ink);
  }
  .base-band {
    position: absolute; left: 0; right: 0; bottom: 0; height: 16px;
    background: var(--band-dark);
  }
  .base-band .accent {
    position: absolute; left: 42px; top: 0; width: 220px; height: 16px;
    background: var(--brand-red);
  }
</style>
</head>
<body>
<main class="stage">

  <section class="card card--back" aria-label="Card back">
    <div class="back-lockup">
      <span class="mark-square"></span>
      <span class="firm-name">Dario Whitcombe</span>
    </div>
    <p class="tagline">Accounting, Tax &amp; Consulting Services</p>
  </section>

  <section class="card card--front" aria-label="Card front">
    <div class="red-tab"></div>
    <div class="front-lockup">
      <span class="mark-square"></span>
      <span class="firm-name">Dario Whitcombe, CPA, LLC</span>
    </div>
    <p class="credential">Certified Public Accountant</p>

    <div class="person">
      <h1 class="person-name">Dario Whitcombe</h1>
      <p class="person-title">Principal</p>
    </div>
    <div class="rule"></div>

    <ul class="contact-list">
      <li>
        <svg viewBox="0 0 24 24" aria-hidden="true"><path d="M6.6 10.8a15.1 15.1 0 0 0 6.6 6.6l2.2-2.2a1 1 0 0 1 1-.25 11.4 11.4 0 0 0 3.6.57 1 1 0 0 1 1 1V20a1 1 0 0 1-1 1A17 17 0 0 1 3 4a1 1 0 0 1 1-1h3.5a1 1 0 0 1 1 1c0 1.25.2 2.45.57 3.57a1 1 0 0 1-.25 1z"/></svg>
        555-014-2283
      </li>
      <li>
        <svg viewBox="0 0 24 24" aria-hidden="true"><path d="M2 5h20v14H2z M3.5 6.5 12 12.5l8.5-6z" fill-rule="evenodd"/></svg>
        dario@whitcombecpa.com
      </li>
      <li>
        <svg viewBox="0 0 24 24" aria-hidden="true"><path d="M12 2a10 10 0 1 0 0 20 10 10 0 0 0 0-20zm0 2c.9 0 2.2 1.9 2.7 5H9.3C9.8 5.9 11.1 4 12 4zm-5 5H4.5A8 8 0 0 1 8.3 4.9 13 13 0 0 0 7 9zm-2.9 2H7a16 16 0 0 0 0 2H4.1a8 8 0 0 1 0-2zm5.1 0h5.6a14 14 0 0 1 0 2H9.2a14 14 0 0 1 0-2zm7.8 0h2.9a8 8 0 0 1 0 2H17a16 16 0 0 0 0-2zm2.5-2H17a13 13 0 0 0-1.3-4.1A8 8 0 0 1 19.5 9zM4.5 15H7a13 13 0 0 0 1.3 4.1A8 8 0 0 1 4.5 15zm4.8 0h5.4c-.5 3.1-1.8 5-2.7 5s-2.2-1.9-2.7-5zm6.4 4.1A13 13 0 0 0 17 15h2.5a8 8 0 0 1-3.8 4.1z"/></svg>
        www.whitcombecpa.com
      </li>
    </ul>

    <address class="address">
      Dario Whitcombe Cpa Llc<br>
      4120 Alder Crest Road<br>
      Juneau, Alaska 99801
    </address>

    <div class="base-band"><span class="accent"></span></div>
  </section>

</main>
</body>
</html>
```